Tarvex Engineering Rail Sector Brochure

We need a new 3 page folding brochure for Tarvex Engineering Pty Ltd. The organisation is currently supporting customers in Defence, Maritime and Information and Communications Technology companies. We are currently looking to expand our engineering services into the rail sector by providing manpower and consultancy services to railway sector clients.We would like the brochure to be based on an A4 page and look technical with particular focus on communications systems used within the railways. This could include pictures of rail control centres, trains (Australian trains only please), train radio communications equipment, radio antennas, computers and networking equipment. Please use both graphics and photos.The brochure will be provided to potential rail customers and should be clear and uncluttered.The following is our company website: www.tarvexengineering.com.au if you would like more detail on our current work.I have attached the file for our logo which should appear on the brochure.
Target Market(s)
Providing manpower and consultancy services to the railway sector. This includes rail companies (e.g. Quillane Transit Lines, K/Rail etc) and rail equipment and carriage suppliers (e.g. Feltmark)
Colors
Designer to choose colors to be used in the design.
Requirements
Must have
- Instead of having "lorem ipsum" text in the brochure you can please use some of the text in the file we have provided. Not all has to be used, and you should not be limited to what is in the file.
Nice to have
- Mixture of different font sizes to highlight particular text elements.

```html
<!DOCTYPE html>
<html lang="en">
<head>
<meta charset="utf-8">
<title>Tarvex Engineering Rail Sector Brochure</title>
<link rel="stylesheet" href="https://fonts.googleapis.com/css2?family=Open+Sans:wght@400;600;700;800&display=swap">
<style>
  :root {
    --backdrop: #262626;
    --brand-blue: #1a45b8;
    --brand-blue-deep: #12318a;
    --paper: #eef3f8;
    --ink: #101c3a;
    --white: #ffffff;
    --band-dark: #1c1c1e;
  }
  * { margin: 0; padding: 0; box-sizing: border-box; }
  html, body { width: 1200px; height: 800px; overflow: hidden; background: var(--backdrop); }
  body { font-family: "Open Sans", sans-serif; }
  .brochure {
    position: absolute; left: 40px; top: 40px; width: 1120px; height: 720px;
    background: var(--paper); overflow: hidden;
  }
  .brochure-art { position: absolute; inset: 0; }
  .panel { position: absolute; top: 0; width: 373.33px; height: 720px; }
  .panel--inside-left { left: 0; }
  .panel--inside-middle { left: 373.33px; }
  .panel--cover { left: 746.66px; }

  /* inside left panel */
  .services-intro {
    position: absolute; left: 34px; top: 46px; width: 318px;
    color: var(--white); font-weight: 700; font-size: 15px; line-height: 1.38;
  }
  .accent-dash { display: block; width: 26px; height: 4px; border-radius: 2px; background: var(--white); margin: 12px 0 0; }
  .accent-dash--blue { background: var(--brand-blue); margin: 6px auto 10px; }
  .service-list {
    list-style: none; position: absolute; left: 34px; top: 172px; width: 316px;
    color: var(--white); font-size: 11px; line-height: 1.4;
  }
  .service-list li { position: relative; padding-left: 16px; margin-bottom: 7px; }
  .service-list li::before { content: "\2713"; position: absolute; left: 0; top: 0; font-weight: 700; }
  .heritage-statement {
    position: absolute; left: 34px; top: 478px; width: 310px;
    color: var(--ink); font-weight: 600; font-size: 17px; line-height: 1.34;
  }

  /* inside middle panel */
  .capabilities {
    position: absolute; left: 38px; top: 128px; width: 297px;
    color: var(--white); font-size: 10px; line-height: 1.5; text-align: center;
  }
  .capabilities p + p { margin-top: 10px; }
  .contact-box {
    position: absolute; left: 76px; top: 340px; width: 222px; padding: 11px 10px;
    border: 1px solid rgba(255,255,255,0.8); border-radius: 12px;
    color: var(--white); font-size: 10px; line-height: 1.45; text-align: center;
  }
  .contact-box strong { display: block; font-weight: 700; font-size: 11px; margin-bottom: 4px; }
  .contact-box strong:last-child { margin-bottom: 0; }
  .office { position: absolute; left: 30px; top: 590px; width: 313px; text-align: center; color: var(--ink); }
  .office-title { font-weight: 800; font-size: 13px; }
  .office-line { font-size: 10.5px; line-height: 1.7; display: flex; align-items: center; justify-content: center; gap: 5px; }
  .office-line svg { width: 10px; height: 10px; flex: none; }

  /* cover panel */
  .wordmark {
    position: absolute; left: 0; top: 52px; width: 373px;
    display: flex; align-items: center; justify-content: center; gap: 10px;
    color: var(--brand-blue-deep); font-weight: 700; font-size: 23px;
  }
  .wordmark-square { width: 20px; height: 20px; background: var(--brand-blue); }
  .cover-headline {
    position: absolute; left: 44px; top: 244px; width: 300px;
    color: var(--white); font-weight: 800; font-size: 25px; line-height: 1.12; text-transform: uppercase;
  }
  .cover-headline .accent-dash { margin: 16px 0 0 8px; }
  .cover-tagline { position: absolute; left: 90px; top: 392px; width: 250px; color: var(--white); font-weight: 700; font-size: 16px; line-height: 1.3; }
  .cover-subline { position: absolute; left: 110px; top: 460px; width: 230px; color: var(--white); font-size: 11px; line-height: 1.4; }
  .web-band {
    position: absolute; left: 110px; top: 502px; width: 230px; height: 24px;
    background: var(--band-dark); color: var(--white); font-size: 10px; line-height: 24px; text-align: center;
  }
  .web-band b { font-weight: 700; }
</style>
</head>
<body>
<main class="brochure">
  <svg class="brochure-art" viewBox="0 0 1120 720" width="1120" height="720">
    <defs>
      <linearGradient id="trackTone" x1="0" y1="0" x2="1" y2="1">
        <stop offset="0" stop-color="#a9c3d8"/>
        <stop offset="1" stop-color="#dfe9f1"/>
      </linearGradient>
      <linearGradient id="trainTone" x1="0" y1="0" x2="1" y2="1">
        <stop offset="0" stop-color="#2d55bf"/>
        <stop offset="0.5" stop-color="#2149b0"/>
        <stop offset="1" stop-color="#1a3e9e"/>
      </linearGradient>
      <linearGradient id="paperTone" x1="0" y1="0" x2="0" y2="1">
        <stop offset="0" stop-color="#e4ecf3"/>
        <stop offset="1" stop-color="#f3f6fa"/>
      </linearGradient>
    </defs>
    <rect width="1120" height="720" fill="url(#paperTone)"/>
    <rect x="0" y="360" width="373.33" height="360" fill="url(#trackTone)" role="img" aria-label="Faded photo of rail tracks and overhead wiring leading to a rail control centre"/>
    <path d="M0 0 H373.33 V430 Q190 360 0 400 Z" fill="var(--brand-blue)"/>
    <path d="M373.33 0 Q560 150 760 120 Q950 95 1120 230 V600 Q1000 560 900 570 Q760 585 640 530 Q500 470 373.33 560 Z" fill="url(#trainTone)" role="img" aria-label="Photo of an Australian suburban passenger train, tinted blue"/>
    <path d="M373.33 560 Q500 470 640 530 Q700 555 746.66 565 V720 H373.33 Z" fill="#dbe6ef" role="img" aria-label="Faint photo of a trackside train radio antenna mast"/>
    <line x1="373.33" y1="0" x2="373.33" y2="720" stroke="rgba(0,0,0,0.08)"/>
    <line x1="746.66" y1="0" x2="746.66" y2="720" stroke="rgba(0,0,0,0.08)"/>
  </svg>

  <section class="panel panel--inside-left">
    <h2 class="services-intro">Tarvex Engineering provides engineering resources, speciality services and project delivery from concept to completion in areas including:
      <span class="accent-dash"></span>
    </h2>
    <ul class="service-list">
      <li>Command and Control (C2) system integration</li>
      <li>Plain and Secure voice &amp; data TCP/IP communications</li>
      <li>Acoustics, Noise, Shock and Vibration design, analysis and test</li>
      <li>RF System Visualisation, Modelling and Analytics</li>
      <li>Networked systems including VoIP, IPTV, CCTV and Videowall technologies</li>
      <li>Logistics, Training and ongoing program support solutions</li>
    </ul>
    <p class="heritage-statement">Tarvex Engineering staff have been in the forefront of major program deliveries to defence and commercial customers for decades. Our staff are leaders in their field and pioneers in the establishment of systematic approaches to the most complex problems.</p>
  </section>

  <section class="panel panel--inside-middle">
    <div class="capabilities">
      <p>At Tarvex Engineering we have a broad mix of capabilities, including abilities in the areas of networking, communications, C2 system integration with sensor and communications systems. Our staff have supported the largest telecommunications networks in Australia and aided defence in building real-time, secure data networks for communications and data sharing. We have enabled communications across multiple platforms types including aircraft, rail, ship and vehicle platforms that operate reliably under extreme environmental conditions.</p>
      <p>At Tarvex Engineering, we are committed to delivering value to all our customers and end users in a manner that inspires.</p>
    </div>
    <div class="contact-box">
      Career Opportunities:<strong>jobs@tarvexengineering.com.au</strong>
      General Enquiries:<strong>info@tarvexengineering.com.au</strong>
    </div>
    <div class="office">
      <h3 class="office-title">Main Office Address:</h3>
      <span class="accent-dash accent-dash--blue"></span>
      <p class="office-line">
        <svg viewBox="0 0 10 10"><path d="M5 0.5a3.2 3.2 0 0 1 3.2 3.2C8.2 6 5 9.5 5 9.5S1.8 6 1.8 3.7A3.2 3.2 0 0 1 5 0.5z" fill="var(--brand-blue)"/><circle cx="5" cy="3.7" r="1.2" fill="#fff"/></svg>
        Level 4, 18 Harrow Lane, Brenmoor 3000
      </p>
      <p class="office-line">
        <svg viewBox="0 0 10 10"><circle cx="5" cy="5" r="4.3" fill="none" stroke="var(--brand-blue)" stroke-width="1"/><ellipse cx="5" cy="5" rx="1.9" ry="4.3" fill="none" stroke="var(--brand-blue)" stroke-width="0.8"/><line x1="0.7" y1="5" x2="9.3" y2="5" stroke="var(--brand-blue)" stroke-width="0.8"/></svg>
        www.tarvexengineering.com.au
      </p>
    </div>
  </section>

  <section class="panel panel--cover">
    <div class="wordmark"><span class="wordmark-square"></span>Tarvex Engineering</div>
    <h1 class="cover-headline">Smart<br>solutions that<br>deliver<br>excellence.<span class="accent-dash"></span></h1>
    <p class="cover-tagline">We deliver solutions to critical challenges.</p>
    <p class="cover-subline">A trusted provider to the world's most exacting customers.</p>
    <p class="web-band">www.<b>tarvexengineering</b>.com.au</p>
  </section>
</main>
</body>
</html>
```